Harborview Estates Business Card for Apartment Buildings

Create business cards for resident managers who run apartment buildings. The audience is the public who are searching for apartment rentals, and current residents who live at the apartment building. Key design element will be incorporating the company logo, however, the logo cannot dominate. The building name and manager name are more important than the logo. Current business card design leaves little room for copy, so we may need to reduce the size on the current card to allow for more space for copy.

Target Market(s)

Adults 18-65 years of age, who are looking for an apartment rental, plus current residents who live at our apartment buildings.

Industry/Entity Type

Property Management

Contact Information for Business Card

A major design element will be use of the company logo. Important property and manager contact information must be part of the design. The size of the logo will need to be reduced to make room for building and manager contact copy.

Font styles to use
Sans Serif

Colors
3176b5
000000
959595
ffffff

Requirements
Must have
• 1) Incorporate the company logo.
• 2) Use the company colors (dark blue, black/grey, over white).
• 3) FEATURE THE BUILDING NAME
• 4) FEATURE THE MANAGER NAME
• 5) The company name is less important than BUILDING and MANAGER
• 6) Manager contact information
• **SEE ATTACHED CREATIVE BRIEF**
Nice to have
• 1) Back of card logo watermark
• 2) Ability to write notes on back of carfd
Should not have
• Avoid letting the company logo dominate the card, the building name and manager are more important than the company logo.

```html
<!DOCTYPE html>
<html lang="en">
<head>
<meta charset="utf-8">
<title>Harborview Estates – Resident Manager Business Card</title>
<link rel="stylesheet" href="https://fonts.googleapis.com/css2?family=Roboto+Condensed:wght@700&family=Roboto:wght@400&display=swap">
<style>
  :root {
    --brand-blue: #1f69a6;
    --band-blue: #0f66a3;
    --band-grey: #444446;
    --text-grey: #444444;
    --card-white: #f4f4f4;
    --watermark-blue: #dfe7ef;
    --watermark-grey: #e2e2e2;
    --backdrop: #262626;
  }
  * { box-sizing: border-box; margin: 0; padding: 0; }
  html, body { width: 1200px; height: 960px; overflow: hidden; }
  body {
    background: var(--backdrop);
    position: relative;
    font-family: "Roboto", Arial, sans-serif;
    color: var(--text-grey);
  }
  .card {
    position: absolute;
    width: 600px;
    height: 343px;
    background: var(--card-white);
    overflow: hidden;
  }
  .card--front { left: 314px; top: 113px; }
  .card--back  { left: 311px; top: 472px; }

  .manager-name {
    position: absolute; left: 41px; top: 40px;
    font-family: "Roboto Condensed", "Arial Narrow", sans-serif;
    font-weight: 700; font-size: 23px; color: var(--brand-blue);
  }
  .manager-title {
    position: absolute; left: 41px; top: 67px;
    font-size: 15px; color: var(--text-grey);
  }
  .contact-list {
    position: absolute; left: 42px; top: 106px;
    list-style: none;
  }
  .contact-list li {
    display: flex; align-items: center; gap: 7px;
    height: 19px; font-size: 14.5px; color: var(--text-grey);
  }
  .contact-list svg { width: 14px; height: 14px; fill: var(--brand-blue); flex: none; }

  .building-name {
    position: absolute; left: 41px; top: 196px;
    font-family: "Roboto Condensed", "Arial Narrow", sans-serif;
    font-weight: 700; font-size: 21px; color: var(--brand-blue);
  }
  .building-address {
    position: absolute; left: 41px; top: 222px;
    font-size: 14.5px; line-height: 19px; font-style: normal; color: var(--text-grey);
  }

  .company-mark {
    position: absolute; left: 318px; top: 48px;
    display: flex; align-items: center; gap: 12px;
  }
  .company-mark__dot {
    width: 40px; height: 40px; border-radius: 50%; background: var(--brand-blue); flex: none;
  }
  .company-mark__name {
    font-family: "Roboto Condensed", "Arial Narrow", sans-serif;
    font-weight: 700; font-size: 25px; line-height: 24px; color: var(--brand-blue);
    letter-spacing: 0.5px;
  }

  .web-band {
    position: absolute; left: 0; top: 282px; width: 600px; height: 32px;
    display: flex;
  }
  .web-band__url {
    width: 471px; background: var(--band-blue);
    color: #ffffff; font-size: 14px; letter-spacing: 2.4px;
    padding-left: 41px; line-height: 32px;
  }
  .web-band__end {
    flex: 1; background: var(--band-grey); position: relative;
  }
  .web-band__dot {
    position: absolute; left: 2px; top: 3px;
    width: 26px; height: 26px; border-radius: 50%; background: #ffffff;
  }

  .back-watermark {
    position: absolute; left: 0; top: 0; width: 600px; height: 343px;
    display: flex; align-items: center; justify-content: center;
  }
  .back-watermark__name {
    font-family: "Roboto Condensed", "Arial Narrow", sans-serif;
    font-weight: 700; font-size: 58px; line-height: 60px; text-align: center;
    color: var(--watermark-blue); letter-spacing: 2px;
  }
</style>
</head>
<body>

<section class="card card--front" aria-label="Business card front">
  <h1 class="manager-name">Marisol Delgado</h1>
  <p class="manager-title">Resident Manager</p>

  <ul class="contact-list">
    <li>
      <svg viewBox="0 0 16 16" aria-hidden="true"><path d="M3.6 1.2l2.2 2.6c.3.4.3.9 0 1.3L4.7 6.3c.9 2 2.9 4 5 5l1.2-1.1c.4-.3.9-.3 1.3 0l2.6 2.2c.4.3.4.9 0 1.3l-1.3 1.3c-.6.6-1.5.8-2.3.5C6.4 14 2 9.6.5 4.8.2 4 .4 3.1 1 2.5L2.3 1.2c.4-.4 1-.4 1.3 0z"/></svg>
      555-210-4387
    </li>
    <li>
      <svg viewBox="0 0 16 16" aria-hidden="true"><path d="M4.5 0h7c.8 0 1.5.7 1.5 1.5v13c0 .8-.7 1.5-1.5 1.5h-7C3.7 16 3 15.3 3 14.5v-13C3 .7 3.7 0 4.5 0zm.5 2v10h6V2H5zm3 11a1 1 0 100 2 1 1 0 000-2z"/></svg>
      555-384-9126
    </li>
    <li>
      <svg viewBox="0 0 16 16" aria-hidden="true"><path d="M4 1h8v4H4zM1 6h14v6h-3v-2H4v2H1zM5 11h6v4H5z"/></svg>
      555-617-3050
    </li>
    <li>
      <svg viewBox="0 0 16 16" aria-hidden="true"><path d="M1 3h14v10H1zM2 4.2v.6l6 4 6-4v-.6l-6 4z" fill-rule="evenodd"/></svg>
      marisol@harborviewest.com
    </li>
  </ul>

  <h2 class="building-name">Cedar Court Apartments</h2>
  <address class="building-address">
    2185 Linden Avenue<br>
    Bayside, CA 90412
  </address>

  <div class="company-mark">
    <span class="company-mark__dot" aria-hidden="true"></span>
    <span class="company-mark__name">HARBORVIEW<br>ESTATES</span>
  </div>

  <div class="web-band">
    <div class="web-band__url">www.harborviewest.com</div>
    <div class="web-band__end"><span class="web-band__dot" aria-hidden="true"></span></div>
  </div>
</section>

<section class="card card--back" aria-label="Business card back">
  <div class="back-watermark">
    <span class="back-watermark__name">HARBORVIEW<br>ESTATES</span>
  </div>
</section>

</body>
</html>
```